BRAVO Estate Attendant

We require a website built for this company. Logo is also on the attached document. Some info on the company:<br/>To create a work class experience for our clients for property maintenance. A personalised service that deliver’s what landlords need...Quality work, on time and managed from start to finish.<br/>We do things different, our clients deal with one contact, a client manager who manages your maintenance task from start to finish. Our service allows our expert trades people to do what they do best and leave the management/organising to us!<br/>I have drafted up the layout of the web ... very brief at this stage however once we have more info we will add links and can collate more information and provide. <br/>We just want to get a layout of what you think the web should look like and can go from there.

```html
<!DOCTYPE html>
<html lang="en">
<head>
<meta charset="utf-8">
<title>BRAVO Estate Attendant</title>
<link rel="stylesheet" href="https://fonts.googleapis.com/css2?family=Montserrat:wght@400;500;600;700&family=Open+Sans:wght@400;600&display=swap">
<style>
:root{
  --yellow:#fdb813;
  --dark:#333333;
  --darker:#1c1c1c;
  --ink:#222222;
  --body:#555555;
  --grey-band:#d9d9d9;
  --white:#ffffff;
  --muted:#8a8a8a;
}
*{box-sizing:border-box;margin:0;padding:0}
html,body{width:1200px;height:3432px;overflow:hidden}
body{position:relative;background:var(--white);font-family:"Open Sans",Arial,sans-serif;color:var(--body)}
.abs{position:absolute}
.heading{font-family:"Montserrat",Arial,sans-serif;font-weight:600;color:var(--ink);text-transform:uppercase}
.rule{position:absolute;height:4px;width:120px;background:var(--yellow)}

/* header */
.header-left{left:0;top:0;width:600px;height:88px;background:var(--dark)}
.header-right{left:600px;top:0;width:600px;height:88px;background:var(--yellow)}
.brand{font-family:"Montserrat",Arial,sans-serif;font-weight:500;color:var(--white);font-size:24px;letter-spacing:1px;line-height:30px}
.phone{left:878px;top:14px;font-family:"Montserrat",Arial,sans-serif;font-weight:600;font-size:24px;color:var(--dark);display:flex;align-items:center;gap:8px}
.nav{left:650px;top:62px;display:flex;gap:34px;font-family:"Montserrat",Arial,sans-serif;font-weight:600;font-size:14px;color:var(--dark)}
.nav a{color:inherit;text-decoration:none;position:relative}
.nav a.active::after{content:"";position:absolute;left:-6px;right:-6px;bottom:-9px;height:3px;background:var(--dark)}

/* hero */
.hero{left:0;top:88px;width:1200px;height:565px}
.hero-title{left:0;width:1200px;top:308px;text-align:center;font-family:"Montserrat",Arial,sans-serif;font-weight:600;font-size:34px;line-height:41px;color:var(--white)}
.btn-yellow{left:493px;top:410px;width:214px;height:47px;background:var(--yellow);font-family:"Montserrat",Arial,sans-serif;font-weight:500;font-size:19px;color:var(--dark);display:flex;align-items:center;justify-content:center}
.arrow{top:334px}

/* welcome */
.welcome-text{left:144px;top:870px;width:437px;font-size:13px;line-height:24px}
.btn-dark{background:var(--dark);color:var(--white);font-family:"Montserrat",Arial,sans-serif;font-size:13px;display:flex;align-items:center;justify-content:center}
.welcome-photo{left:623px;top:759px;width:424px;height:344px;background:linear-gradient(135deg,#c9c2b6 0%,#e8e4de 40%,#8a6a4c 75%,#5b3e27 100%);box-shadow:8px 8px 0 var(--dark)}

/* services */
.card{background:var(--white);width:297px;height:172px;display:flex;flex-direction:column;align-items:center}
.card svg{margin-top:30px}
.card span{margin-top:16px;font-family:"Montserrat",Arial,sans-serif;font-weight:500;font-size:16px;color:var(--ink)}

/* why */
.why-photo{left:144px;top:1939px;width:431px;height:552px;background:linear-gradient(180deg,#6f9a4a 0%,#9bb57a 25%,#b9a88c 55%,#c0503e 80%,#6fa43b 100%);box-shadow:-8px 8px 0 var(--dark)}
.feature{left:623px;display:flex;align-items:center;gap:16px}
.feature .dot{width:80px;height:80px;border-radius:50%;background:var(--yellow);display:flex;align-items:center;justify-content:center}
.feature b{font-family:"Montserrat",Arial,sans-serif;font-weight:700;font-size:22px;color:var(--ink)}

/* contact */
.field{background:var(--white);border:1px solid #cfcfcf;font-size:13px;color:#777;padding:0 22px;display:flex;align-items:center}

/* footer */
.footer{left:0;top:3130px;width:1200px;height:302px;background:var(--darker)}
.foot-col h4{font-family:"Montserrat",Arial,sans-serif;font-weight:500;font-size:16px;color:var(--yellow);margin-bottom:8px}
.foot-col p{font-size:10.5px;color:var(--muted);line-height:24px}
.social{width:40px;height:40px;border:1px solid #666;border-radius:50%}
</style>
</head>
<body>

<!-- header -->
<div class="abs header-left"></div>
<div class="abs header-right"></div>
<div class="abs brand" style="left:143px;top:29px">BRAVO Estate Attendant</div>
<div class="abs phone">
  <svg width="18" height="18" viewBox="0 0 24 24"><path d="M6.6 10.8a15 15 0 0 0 6.6 6.6l2.2-2.2a1 1 0 0 1 1-.25 11 11 0 0 0 3.6.6 1 1 0 0 1 1 1V20a1 1 0 0 1-1 1A17 17 0 0 1 3 4a1 1 0 0 1 1-1h3.5a1 1 0 0 1 1 1 11 11 0 0 0 .6 3.6 1 1 0 0 1-.25 1z" fill="#333"/></svg>
  555 010 2468
</div>
<nav class="abs nav"><a class="active">ABOUT US</a><a>SERVICES</a><a>BENEFIT</a><a>CONTACT US</a></nav>

<!-- hero -->
<svg class="abs hero" width="1200" height="565" viewBox="0 0 1200 565">
  <defs>
    <radialGradient id="heroGlow" cx="50%" cy="40%" r="70%">
      <stop offset="0" stop-color="#6e7479"/>
      <stop offset="0.6" stop-color="#4c5157"/>
      <stop offset="1" stop-color="#2f3338"/>
    </radialGradient>
  </defs>
  <polygon points="0,0 1200,0 1200,565 0,527" fill="url(#heroGlow)" role="img" aria-label="Photo of hands holding a small model house with trees"/>
  <polygon points="0,527 600,546 1200,565 0,565" fill="var(--white)"/>
  <polygon points="0,527 600,546 0,565" fill="var(--yellow)"/>
  <circle cx="600" cy="178" r="24" fill="var(--white)"/>
  <polygon points="594,166 594,190 612,178" fill="#333"/>
</svg>
<div class="abs hero-title">VIVAMUS LACUS JUSTO<br>ULTRICES ERAT</div>
<div class="abs btn-yellow">GET STARTED NOW</div>
<svg class="abs arrow" style="left:60px" width="24" height="30" viewBox="0 0 24 30"><polyline points="18,3 6,15 18,27" fill="none" stroke="#fff" stroke-width="5"/></svg>
<svg class="abs arrow" style="left:1116px" width="24" height="30" viewBox="0 0 24 30"><polyline points="6,3 18,15 6,27" fill="none" stroke="#fff" stroke-width="5"/></svg>

<!-- welcome -->
<h2 class="abs heading" style="left:144px;top:789px;font-size:32px">Welcome</h2>
<div class="rule" style="left:144px;top:844px"></div>
<p class="abs welcome-text">Vestibulum luctus ex in egestas fringilla. Fusce nec leo ac urna pulvinar auctor. Mauris bibendum fringilla velit. Nulla in lorem at massa pellentesque posuere. Nulla tristique posuere molestie. Aliquam erat volutpat. Etiam quis aliquet risus. Duis ornare erat eget magna dapibus, in accumsan quam pharetra. Nam tempus, quam in bibendum vulputate, sapien dolor viverra nisl, vitae euismod elit turpis et nulla.</p>
<div class="abs btn-dark" style="left:144px;top:1032px;width:112px;height:39px">READ MORE</div>
<div class="abs welcome-photo" role="img" aria-label="Photo of a bright hallway with wooden floor, staircase and a bench"></div>

<!-- services -->
<svg class="abs" style="left:0;top:1190px" width="1200" height="668" viewBox="0 0 1200 668">
  <defs>
    <linearGradient id="svcBg" x1="0" y1="0" x2="1" y2="1">
      <stop offset="0" stop-color="#cfcfcf"/><stop offset="0.5" stop-color="#e3e3e3"/><stop offset="1" stop-color="#d2d2d2"/>
    </linearGradient>
  </defs>
  <polygon points="0,3 1200,0 1200,668 0,668" fill="url(#svcBg)" role="img" aria-label="Faded photo of a tradesman in a hard hat at work"/>
  <polygon points="600,20 1200,0 1200,40" fill="var(--yellow)"/>
  <polygon points="0,628 600,648 1200,668 0,668" fill="var(--white)"/>
  <polygon points="0,628 600,648 0,668" fill="var(--yellow)"/>
</svg>
<h2 class="abs heading" style="left:0;width:1200px;text-align:center;top:1300px;font-size:32px">Services</h2>
<div class="rule" style="left:540px;top:1355px"></div>

<div class="abs card" style="left:144px;top:1384px">
  <svg width="66" height="66" viewBox="0 0 66 66" fill="none" stroke="#333" stroke-width="2"><rect x="3" y="4" width="22" height="10"/><rect x="40" y="6" width="18" height="10"/><circle cx="20" cy="24" r="5"/><circle cx="44" cy="24" r="5"/><path d="M10 62V40a8 8 0 0 1 8-8h4a8 8 0 0 1 8 8v22M36 62V40a8 8 0 0 1 8-8h4a8 8 0 0 1 8 8v22"/><path d="M16 62V46M24 62V46M42 62V46M50 62V46"/></svg>
  <span>Trade People</span>
</div>
<div class="abs card" style="left:452px;top:1384px">
  <svg width="90" height="66" viewBox="0 0 90 66" fill="none" stroke="#333" stroke-width="2"><rect x="2" y="8" width="54" height="42"/><path d="M56 22h18l12 14v14H56z"/><path d="M62 26h10l8 10H62z"/><circle cx="20" cy="54" r="6" fill="#fff"/><circle cx="70" cy="54" r="6" fill="#fff"/><path d="M2 2h20"/></svg>
  <span>Removalist van and Trailers</span>
</div>
<div class="abs card" style="left:758px;top:1384px">
  <svg width="70" height="66" viewBox="0 0 70 66" fill="none" stroke="#333" stroke-width="2"><path d="M66 4L46 30M4 22l14 10"/><path d="M18 32l18 18a4 4 0 0 0 6-6M30 42l8 8a4 4 0 0 0 6-6l-4-4M24 36l8 8M46 30l-8-4-12 10a4 4 0 0 0 6 5l8-6 10 10a4 4 0 0 0 6-6"/><path d="M14 30l-6 6 4 4M20 38l-6 6 4 4"/></svg>
  <span>Connections</span>
</div>
<div class="abs card" style="left:144px;top:1566px">
  <svg width="66" height="66" viewBox="0 0 66 66" fill="none" stroke="#333" stroke-width="2"><circle cx="31" cy="31" r="28"/><circle cx="31" cy="31" r="18" stroke-dasharray="3 3"/><circle cx="31" cy="31" r="11"/><circle cx="31" cy="31" r="4"/><circle cx="52" cy="52" r="9" fill="#fff"/><path d="M52 47v6M52 56v1"/></svg>
  <span>Smoke Alarms</span>
</div>
<div class="abs card" style="left:452px;top:1566px">
  <svg width="66" height="66" viewBox="0 0 66 66" fill="none" stroke="#333" stroke-width="2"><rect x="28" y="4" width="30" height="56"/><rect x="34" y="12" width="18" height="30"/><circle cx="43" cy="27" r="6"/><rect x="4" y="40" width="12" height="20"/><path d="M16 44h10l10-6a4 4 0 0 1 4 6l-8 6v10H16"/></svg>
  <span>Finance</span>
</div>
<div class="abs card" style="left:758px;top:1566px">
  <svg width="66" height="66" viewBox="0 0 66 66" fill="none" stroke="#333" stroke-width="2"><path d="M4 30L33 6l29 24M10 26v34h46V26"/><circle cx="33" cy="26" r="4"/><rect x="16" y="38" width="10" height="10"/><rect x="40" y="38" width="10" height="10"/><path d="M28 60V44h10v16M2 60h62M46 10V4h6v11"/></svg>
  <span>Wealth Creation</span>
</div>

<!-- why choose us -->
<div class="abs why-photo" role="img" aria-label="Photo of a family house with a garden and flower beds"></div>
<h2 class="abs heading" style="left:623px;top:1935px;font-size:32px">Why Choose Us?</h2>
<div class="rule" style="left:623px;top:1988px"></div>
<p class="abs" style="left:623px;top:2012px;width:437px;font-size:13px;line-height:24px">Maecenas vel tortor accumsan quam varius imperdiet vel eget elit. Aenean facilisis tincidunt lectus, id dictum nisi luctus eget. Vivamus efficitur ex condimentum, malesuada eros.</p>

<div class="abs feature" style="top:2100px">
  <div class="dot"><svg width="40" height="40" viewBox="0 0 24 24"><path d="M2 10h4v12H2zM8 21V10l5-8c2 0 3 1 2.5 3L14 9h6a2 2 0 0 1 2 2.3l-1.4 8A2 2 0 0 1 18.6 21z" fill="#222"/></svg></div>
  <b>QUALITY WORK</b>
</div>
<div class="abs feature" style="top:2204px">
  <div class="dot"><svg width="40" height="40" viewBox="0 0 24 24"><circle cx="12" cy="12" r="10" fill="#222"/><path d="M12 6v6h4" stroke="#fdb813" stroke-width="2" fill="none"/></svg></div>
  <b>ON TIME</b>
</div>
<div class="abs feature" style="top:2308px">
  <div class="dot"><svg width="40" height="40" viewBox="0 0 24 24" fill="none" stroke="#222" stroke-width="2.4" stroke-linecap="round"><path d="M4 20L16 8"/><path d="M14 4a4 4 0 0 0 6 6"/><path d="M4 4l16 16"/><path d="M3 7l4-4"/></svg></div>
  <b>MAINTENANCE AND REPAIRS</b>
</div>
<div class="abs feature" style="top:2412px">
  <div class="dot"><svg width="40" height="40" viewBox="0 0 24 24"><path d="M2 11L11 3l9 8h-3v10H5V11z" fill="#222"/><path d="M15 12l5 2v3c0 3-2.5 4.5-5 5.5-2.5-1-5-2.5-5-5.5v-3z" fill="#fdb813" stroke="#222" stroke-width="1.4"/></svg></div>
  <b>INSURANCES</b>
</div>

<!-- contact -->
<svg class="abs" style="left:0;top:2573px" width="1200" height="557" viewBox="0 0 1200 557">
  <defs>
    <linearGradient id="ctBg" x1="0" y1="0" x2="1" y2="1">
      <stop offset="0" stop-color="#d6d6d6"/><stop offset="0.5" stop-color="#e6e6e6"/><stop offset="1" stop-color="#d0d0d0"/>
    </linearGradient>
  </defs>
  <polygon points="0,3 1200,0 1200,557 0,557" fill="url(#ctBg)" role="img" aria-label="Faded photo of removal workers beside a van"/>
  <polygon points="600,20 1200,0 1200,40" fill="var(--yellow)"/>
  <polygon points="0,517 600,537 1200,557 0,557" fill="var(--darker)"/>
  <polygon points="0,517 600,537 0,557" fill="var(--yellow)"/>
</svg>
<h2 class="abs heading" style="left:0;width:1200px;text-align:center;top:2684px;font-size:32px">Contact Us</h2>
<div class="rule" style="left:540px;top:2738px"></div>
<div class="abs field" style="left:144px;top:2768px;width:447px;height:51px">Name</div>
<div class="abs field" style="left:144px;top:2832px;width:447px;height:51px">Email</div>
<div class="abs field" style="left:144px;top:2896px;width:447px;height:51px">Phone</div>
<div class="abs field" style="left:607px;top:2768px;width:448px;height:179px;align-items:flex-start;padding-top:16px">Message</div>
<div class="abs btn-dark" style="left:543px;top:2973px;width:112px;height:38px">SUBMIT</div>

<!-- footer -->
<div class="abs footer"></div>
<div class="abs brand" style="left:144px;top:3200px;color:#bdbdbd">BRAVO Estate Attendant</div>
<div class="abs social" style="left:144px;top:3263px"></div>
<div class="abs social" style="left:200px;top:3263px"></div>
<div class="abs social" style="left:256px;top:3263px"></div>

<div class="abs foot-col" style="left:388px;top:3178px"><h4>ABOUT US</h4><p>Team<br>Concept<br>Location</p></div>
<div class="abs foot-col" style="left:523px;top:3178px"><h4>SERVICES</h4><p>Trade people<br>Removalist van and trailers<br>Connections<br>Smoke alarms<br>Finance<br>Wealth creation</p></div>
<div class="abs foot-col" style="left:715px;top:3178px"><h4>BENEFIT</h4><p>Customer service<br>Call centre<br>Values<br>Pricing<br>Level of expertise</p></div>
<div class="abs foot-col" style="left:882px;top:3178px">
  <h4>CONTACT INFO</h4>
  <p style="display:flex;gap:14px;line-height:16px;padding-top:4px"><svg width="10" height="14" viewBox="0 0 10 14"><path d="M5 0a5 5 0 0 1 5 5c0 4-5 9-5 9S0 9 0 5a5 5 0 0 1 5-5z" fill="#8a8a8a"/><circle cx="5" cy="5" r="2" fill="#1c1c1c"/></svg><span>24 Sample Lane, Harbour Road,<br>Riverton 4021</span></p>
  <p style="display:flex;gap:14px;margin-top:10px;line-height:20px"><svg width="11" height="11" viewBox="0 0 24 24" style="margin-top:5px"><path d="M6.6 10.8a15 15 0 0 0 6.6 6.6l2.2-2.2a1 1 0 0 1 1-.25 11 11 0 0 0 3.6.6 1 1 0 0 1 1 1V20a1 1 0 0 1-1 1A17 17 0 0 1 3 4a1 1 0 0 1 1-1h3.5a1 1 0 0 1 1 1 11 11 0 0 0 .6 3.6 1 1 0 0 1-.25 1z" fill="#8a8a8a"/></svg><span>555 010 1357</span></p>
  <p style="display:flex;gap:14px;line-height:20px"><svg width="11" height="9" viewBox="0 0 11 9" style="margin-top:6px"><rect width="11" height="9" fill="#8a8a8a"/><path d="M0 0l5.5 5L11 0" stroke="#1c1c1c" fill="none"/></svg><span>hello@bravoestate.example</span></p>
</div>

<div class="abs" style="left:144px;top:3376px;width:912px;height:1px;background:#444"></div>
<p class="abs" style="left:0;width:1200px;top:3395px;text-align:center;font-size:11px;color:var(--muted)">Copyright &copy; 2019 BRAVO Estate Attendant. &nbsp; All rights reserved.</p>

</body>
</html>
```